Broschüre für Personaldienstleister
Zielgruppe
Wir sind ein Personaldienstleister und vermitteln ausländisches medizinisches Fachpersonal an deutsche Einrichtungen. Unsere Zielgruppe sind Krankenhäuser, Pflegeheime, Ärztehäuser, Praxen, Labore und weitere medizinische Institutionen.
Aufgabenstellung
Wir haben eine Infobroschüre sowie eine PowerPoint Präsentation bereits mit einem groben Design erstellt. Texte und Beispielbilder (Stockmaterial) sind ebenfalls vorhanden, gerne wünschen wir uns auch Eigeninitiative bei der Wahl der Bilder passend zum neuen Design.
Wir wünschen uns ein Redesign mit einem kreativen, einzigartigen Design. Zudem ist uns wichtig, dass unsere Infografiken qualitativ und hochwertig gestaltet werden.
Dieses Projekt ist mit zukünftigen Folgeprojekten verbunden, da wir weitere Präsentationen und Broschüren für andere Zielgruppen benötigen.

```html
<!DOCTYPE html>
<html lang="de">
<head>
<meta charset="utf-8">
<title>Corven HR – Fachkräfteeinwanderungsgesetz</title>
<link rel="stylesheet" href="https://fonts.googleapis.com/css2?family=Roboto:wght@300;400;500&family=Roboto+Condensed:wght@300;400;700&family=Montserrat:wght@700&display=swap">
<style>
  :root{
    --black:#000;
    --white:#fff;
    --gutter:#6b6b6b;
    --frame:#d9d9d9;
    --teal-dark:#1f4747;
    --teal:#1c4a4c;
    --text-grey:#5a5a5a;
    --wall:#4a4a4a;
  }
  *{margin:0;padding:0;box-sizing:border-box}
  html,body{width:1200px;height:833px;overflow:hidden;background:var(--frame)}
  .spread{position:relative;width:1200px;height:833px;background:var(--frame)}
  .gutter{position:absolute;left:594px;top:0;width:14px;height:833px;background:var(--gutter)}

  /* left page */
  .page-cover{position:absolute;left:8px;top:6px;width:581px;height:822px;background:var(--black);overflow:hidden}
  .brand{position:absolute;left:23px;top:24px;color:var(--white);font-family:"Montserrat",sans-serif;font-weight:700;font-size:30px;letter-spacing:-0.5px}
  .brand-rule{position:absolute;left:23px;top:64px;width:264px;height:2px;background:var(--white)}
  .cover-title{position:absolute;left:23px;top:72px;width:330px;color:var(--white);font-family:"Roboto",sans-serif;font-weight:500;font-size:15.5px;line-height:18.7px}
  .cover-intro{position:absolute;left:23px;top:129px;width:320px;color:var(--white);font-family:"Roboto Condensed",sans-serif;font-weight:400;font-size:11.2px;line-height:14px;letter-spacing:-0.45px;text-align:justify}
  .cover-photo{position:absolute;left:0;top:262px;width:581px;height:560px;
    background:radial-gradient(ellipse at 55% 35%,#8a4f22 0%,#5a3014 25%,#1a0d05 50%,#000 70%),
               linear-gradient(#000 55%,#d8d8d8 80%,#8a1a1a 100%);
    background-blend-mode:screen}

  /* right page */
  .page-facts{position:absolute;left:613px;top:6px;width:582px;height:822px;background:var(--white)}
  .facts-header{position:absolute;left:0;top:0;width:582px;height:231px;
    background:linear-gradient(180deg,#3f3f3f 0%,#5a5a5a 55%,#6a6a6a 80%,#e2e2e2 82%,#bdbdbd 100%)}
  .badge{position:absolute;left:15px;top:14px;width:70px;height:70px;border-radius:50%;background:var(--teal);border:3px solid #cfe6dc}
  .facts-title{position:absolute;left:204px;top:82px;color:var(--white);font-family:"Roboto Condensed",sans-serif;font-weight:700;font-size:33px;letter-spacing:0.2px}

  .facts-col{position:absolute;top:259px;list-style:none;display:flex;flex-direction:column;gap:14px}
  .facts-col::before{content:"";position:absolute;left:9px;top:10px;bottom:40px;border-left:1px dashed var(--teal)}
  .facts-col--left{left:26px;width:250px}
  .facts-col--right{left:302px;width:260px}
  .fact{position:relative;padding-left:27px;font-family:"Roboto",sans-serif;font-weight:400;font-size:11.6px;line-height:14.1px;color:var(--text-grey)}
  .fact::before{content:"";position:absolute;left:0;top:0;width:19px;height:19px;border-radius:50%;background:var(--white);border:1.3px solid var(--teal)}
  .fact::after{content:"";position:absolute;left:4.5px;top:4.5px;width:10px;height:10px;border-radius:50%;background:var(--teal)}

  .facts-footer{position:absolute;left:0;top:795px;width:582px;height:27px;background:var(--teal-dark);color:var(--white);font-family:"Roboto",sans-serif;font-size:7.6px}
  .facts-footer span{position:absolute;top:9px}
</style>
</head>
<body>
<div class="spread">
  <section class="page-cover">
    <div class="brand">Corven HR</div>
    <div class="brand-rule"></div>
    <h1 class="cover-title">Deutschlands neues Fachkräfteeinwanderungsgesetz für 2023</h1>
    <p class="cover-intro">Am 30. November 2022 hat die deutsche Bundesregierung die Eckpunkte des neuen Fachkräfteeinwanderungsgesetztes verabschiedet. Damit will Deutschland massiv die Bildungschancen verbessern, Aus- und Weiterbildung gezielt voranbringen sowie die Einwanderung für Fachkräfte erheblich erleichtern – insbesondere für Personen aus Drittstaaten und somit auch für erwerbstätige Menschen aus der Türkei.<br>Wir haben die wichtigsten Fakten für Sie übersichtlich im Folgenden zusammengefasst.</p>
    <div class="cover-photo" role="img" aria-label="Foto: Richterhammer aus Holz auf einem aufgeschlagenen Gesetzbuch vor schwarzem Hintergrund"></div>
  </section>

  <div class="gutter"></div>

  <section class="page-facts">
    <div class="facts-header" role="img" aria-label="Foto: großes weißes Paragrafenzeichen vor grauer Wand auf hellem Holzboden"></div>
    <div class="badge"></div>
    <h2 class="facts-title">Die Fakten im Überblick</h2>

    <ul class="facts-col facts-col--left">
      <li class="fact">Menschen aus Drittstaaten mit einem deutschen oder einem in Deutschland anerkannten Abschluss sollen fortan jede qualifizierte Beschäftigung ausüben können. Ein Beispiel: eine als Kauffrau für Büromanagement anerkannte Fachkraft kann auch im Bereich Logistik als Fachkraft beschäftigt werden.</li>
      <li class="fact">Stärkung der Bildungsmigration, indem die Aufnahme einer Berufsausbildung oder eines Studiums erleichtert wird</li>
      <li class="fact">Für die „Blaue Karte EU“ wird die Gehaltsschwelle abgesenkt und somit attraktiver für Berufsanfänger:innen</li>
      <li class="fact">In Zukunft soll ein ausländischer Berufs- oder Hochschulabschluss (mind. 2 Jahre) und eine mindestens zweijährige Berufserfahrung in dem angestrebten (nicht-reglementierten) Beruf für einen Aufenthalt zur Erwerbstätigkeit ausreichen die formale Anerkennung des ausländischen Berufsabschlusses ist nicht erforderlich</li>
      <li class="fact">Für Fachkräfte aus Drittstaaten besteht die Möglichkeit erst nach der Einreise die Anerkennung ihres ausländischen Berufsabschlusses anerkennen zu lassen und nebenher bereits eine qualifizierte Beschäftigung auszuüben</li>
    </ul>

    <ul class="facts-col facts-col--right">
      <li class="fact">Die Chancenkarte ist neu und richtet sich an qualifizierte Drittstaatsangehörige, die noch keinen Arbeitsvertrag haben. Sie garantiert einen Aufenthaltstitel für bis zu einem Jahr für die Arbeitssuche in Deutschland und berechtigt bereits zu Probe- bzw. Nebenbeschäftigungen</li>
      <li class="fact">Basieren soll die sogenannte Chancenkarte auf Basis eines Punktesystems, ähnlich dem von Kanada. Zu den Auswahlkriterien gehören die QUALIFIKATION, SPRACHKENNTNISSE, BERUFSERFAHRUNG, DEUTSCHLANDBEZUG und das ALTER.</li>
      <li class="fact">Zudem ist die Kurzzeitig befristete Beschäftigungen im Rahmen von Kontingenten geplant, ohne spezielle Qualifikationsanforderungen</li>
      <li class="fact">Die Sprachförderung im In- und Ausland soll deutlich ausgebaut werden</li>
      <li class="fact">Das Anerkennungsverfahren, das Beschleunigte Fachkräfteverfahren sowie das Visumverfahren sollen optimiert und die Bearbeitungszeiten strikter eingehalten werden</li>
      <li class="fact">Erleichterung der Einbürgerung: Die Mindestaufenthaltsdauer soll von 8 auf 5 Jahre herabgesetzt werden, bei besonderen Integrationsleistungen sogar auf 3 Jahre – außerdem muss die alte Staatsbürgerschaft nicht mehr aufgegeben werden</li>
    </ul>

    <footer class="facts-footer">
      <span style="left:75px">+49 211 555 01 230</span>
      <span style="left:267px">hr@corven-hr.de</span>
      <span style="left:432px">www.corven-hr.de</span>
    </footer>
  </section>
</div>
</body>
</html>
```